Business card for law firm

Need business card for new law firm. Think confident, authoritative, conservative, but not stuffy or old-fashioned.

Contact Information for Business Card

Content for card - logo (uploaded), plus the following:

Paul Whitcombe (larger font)
Managing Partner (larger font, but not as large as name)
Level 9, 7 Ferris Lane
Sydney NSW 2000
Main Tel 02 9364 2710
Direct Tel 02 8472 3159
Email paul@qvlegal.com.au
www.qvlegal.com.au

Letterhead design should include logo plus:
Level 9, 7 Ferris Lane
Sydney NSW 2000
Tel 02 8472 3159
www.qvlegal.com.au

```html
<!DOCTYPE html>
<html lang="en">
<head>
<meta charset="utf-8">
<title>Quayvale Legal — Stationery</title>
<link href="https://fonts.googleapis.com/css2?family=Source+Sans+3:wght@400;700&display=swap" rel="stylesheet">
<style>
  :root {
    --navy: #001a52;
    --ink: #1f1f1f;
    --black: #050505;
    --paper: #ffffff;
    --paper-shade: #ececec;
    --stage-light: #ebecec;
    --stage-dark: #c4c5c8;
    --rule: #b8b8b8;
  }
  * { margin: 0; padding: 0; box-sizing: border-box; }
  html, body {
    width: 1200px; height: 1197px; overflow: hidden;
    font-family: "Source Sans 3", "Myriad Pro", Arial, sans-serif;
    color: var(--ink);
  }
  .stage {
    position: relative;
    width: 1400px; height: 1397px;
    transform: scale(0.857142857);
    transform-origin: 0 0;
    background: linear-gradient(135deg, var(--stage-light) 0%, var(--stage-dark) 100%);
  }

  /* Letterhead */
  .letterhead {
    position: absolute; left: 85px; top: 90px;
    width: 968px; height: 1252px;
    background: linear-gradient(150deg, var(--paper) 0%, var(--paper-shade) 100%);
    border: 1px solid #d4d4d4;
    overflow: hidden;
  }
  .brand { position: absolute; text-align: center; color: var(--navy); font-weight: 400; }
  .brand__mark { display: block; margin: 0 auto; background: var(--navy); }
  .brand__name { display: block; text-transform: uppercase; line-height: 1; }
  .brand__sub { display: block; text-transform: uppercase; line-height: 1; }

  .letterhead .brand { left: 20px; top: 28px; width: 240px; }
  .letterhead .brand__mark { width: 48px; height: 48px; margin-bottom: 22px; }
  .letterhead .brand__name { font-size: 36px; letter-spacing: 2px; }
  .letterhead .brand__sub { font-size: 13px; letter-spacing: 12px; margin-top: 8px; padding-left: 12px; }

  .contact { position: absolute; border-left: 1px solid var(--rule); }
  .contact p { white-space: nowrap; display: flex; align-items: center; }
  .contact .icon { width: 11px; height: 11px; margin-right: 5px; flex: none; }

  .letterhead .contact { left: 761px; top: 52px; padding-left: 16px; height: 90px; font-size: 14.5px; line-height: 20px; }
  .letterhead .contact .gap { margin-top: 11px; }

  /* Footer band: straight navy band under a thin black rule */
  .footer-band {
    position: absolute; left: 0; right: 0; bottom: 0;
    background: var(--navy);
    border-top: solid var(--black);
    box-shadow: 0 -1px 0 var(--paper);
  }
  .letterhead .footer-band { height: 58px; border-top-width: 6px; }
  .card--front .footer-band { height: 22px; border-top-width: 3px; }

  /* Business card front */
  .card { position: absolute; left: 907px; width: 431px; height: 246px; overflow: hidden; }
  .card--front { top: 533px; background: var(--paper); border: 1px solid #d4d4d4; }
  .card--front .brand { left: 40px; top: 57px; width: 192px; }
  .card--front .brand__mark { width: 40px; height: 40px; margin-bottom: 20px; }
  .card--front .brand__name { font-size: 29px; letter-spacing: 1.5px; }
  .card--front .brand__sub { font-size: 10.5px; letter-spacing: 10px; margin-top: 7px; padding-left: 10px; }

  .card--front .contact { left: 244px; top: 42px; height: 143px; padding-left: 17px; font-size: 12px; line-height: 18px; }
  .person__name { font-size: 15px; font-weight: 700; color: var(--navy); line-height: 18px; }
  .person__role { margin-bottom: 4px; }
  .card--front .contact .gap { margin-top: 4px; }

  /* Business card back */
  .card--back { top: 797px; background: var(--navy); color: var(--paper); }
  .card--back .brand { left: 0; right: 0; top: 60px; color: var(--paper); }
  .card--back .brand__mark { width: 56px; height: 56px; background: var(--paper); margin-bottom: 20px; }
  .card--back .brand__name { font-size: 30px; letter-spacing: 3px; }
  .card--back .brand__sub { font-size: 11px; letter-spacing: 10px; margin-top: 8px; padding-left: 10px; }
  .card__url {
    position: absolute; left: 0; right: 0; top: 212px;
    text-align: center; font-size: 11.5px; letter-spacing: 2.4px;
  }
</style>
</head>
<body>
<div class="stage">

  <section class="letterhead" aria-label="Letterhead">
    <div class="brand">
      <span class="brand__mark"></span>
      <span class="brand__name">Quayvale</span>
      <span class="brand__sub">Legal</span>
    </div>

    <div class="contact">
      <p>Level 9, 7 Ferris Lane</p>
      <p>Sydney NSW 2000</p>
      <p class="gap">
        <svg class="icon" viewBox="0 0 12 12"><circle cx="6" cy="6" r="5.2" fill="none" stroke="#1f1f1f" stroke-width="1"/><path d="M4 3.2c-.8.8-.6 2.4.6 3.8s2.8 2 3.6 1.2l-1-1.2-.9.5c-.6-.3-1.4-1.2-1.7-1.8l.5-.9z" fill="#1f1f1f"/></svg>
        02 8472 3159(Direct)
      </p>
      <p>
        <svg class="icon" viewBox="0 0 12 12" fill="none" stroke="#1f3266" stroke-width="1"><circle cx="6" cy="6" r="5"/><ellipse cx="6" cy="6" rx="2.2" ry="5"/><path d="M1 6h10M1.8 3.5h8.4M1.8 8.5h8.4"/></svg>
        www.qvlegal.com.au
      </p>
    </div>

    <div class="footer-band" aria-hidden="true"></div>
  </section>

  <section class="card card--front" aria-label="Business card, front">
    <div class="brand">
      <span class="brand__mark"></span>
      <span class="brand__name">Quayvale</span>
      <span class="brand__sub">Legal</span>
    </div>

    <div class="contact">
      <p class="person__name">Paul Whitcombe</p>
      <p class="person__role">Managing Partner</p>
      <p>Level 9, 7 Ferris Lane</p>
      <p>Sydney NSW 2000</p>
      <p class="gap">
        <svg class="icon" viewBox="0 0 12 12"><circle cx="6" cy="6" r="5.2" fill="none" stroke="#1f1f1f" stroke-width="1"/><path d="M4 3.2c-.8.8-.6 2.4.6 3.8s2.8 2 3.6 1.2l-1-1.2-.9.5c-.6-.3-1.4-1.2-1.7-1.8l.5-.9z" fill="#1f1f1f"/></svg>
        02 9364 2710(Main)
      </p>
      <p>
        <svg class="icon" viewBox="0 0 12 12"><circle cx="6" cy="6" r="5.2" fill="none" stroke="#1f1f1f" stroke-width="1"/><path d="M4 3.2c-.8.8-.6 2.4.6 3.8s2.8 2 3.6 1.2l-1-1.2-.9.5c-.6-.3-1.4-1.2-1.7-1.8l.5-.9z" fill="#1f1f1f"/></svg>
        02 8472 3159(Direct)
      </p>
      <p>
        <svg class="icon" viewBox="0 0 12 12"><rect x="1" y="3" width="10" height="7" fill="#1f3266"/><path d="M1 3l5 4 5-4" fill="none" stroke="#ffffff" stroke-width="1"/></svg>
        paul@qvlegal.com.au
      </p>
      <p>
        <svg class="icon" viewBox="0 0 12 12" fill="none" stroke="#1f3266" stroke-width="1"><circle cx="6" cy="6" r="5"/><ellipse cx="6" cy="6" rx="2.2" ry="5"/><path d="M1 6h10M1.8 3.5h8.4M1.8 8.5h8.4"/></svg>
        www.qvlegal.com.au
      </p>
    </div>

    <div class="footer-band" aria-hidden="true"></div>
  </section>

  <section class="card card--back" aria-label="Business card, back">
    <div class="brand">
      <span class="brand__mark"></span>
      <span class="brand__name">Quayvale</span>
      <span class="brand__sub">Legal</span>
    </div>
    <p class="card__url">www.qvlegal.com.au</p>
  </section>

</div>
</body>
</html>
```